Business Card Design

Electronic Security Installation Specialists

Check out our website at www.tallbrookllc.com to see what we do.

Industry/Entity Type

Business

Contact Information for Business Card

Tall Brook
Marjorie Hadley
281 Orchard Rise
Mapleton, WV 25871

Colors
3176b5
0455a3
ffffff

```html
<!DOCTYPE html>
<html lang="en">
<head>
<meta charset="utf-8">
<title>Tall Brook – Business Card</title>
<link href="https://fonts.googleapis.com/css2?family=Exo+2:wght@400;500;600&display=swap" rel="stylesheet">
<style>
  :root{
    --bg:#e4e4e6;
    --card:#ffffff;
    --ink:#3a3a3c;
    --ink-soft:#555558;
    --blue-deep:#0455a3;
    --blue-bright:#3176b5;
    --blue-navy:#22407f;
    --steel:#58585c;
    --steel-light:#b9b9bd;
  }
  *{margin:0;padding:0;box-sizing:border-box}
  html,body{width:1200px;height:900px;overflow:hidden}
  body{background:var(--bg);font-family:"Exo 2",sans-serif;color:var(--ink);position:relative}
  .card{
    position:absolute;left:150px;top:193px;width:900px;height:514px;
    background:var(--card);overflow:hidden;
    box-shadow:0 18px 40px rgba(0,0,0,.18);
  }
  .card__swoosh{position:absolute;inset:0;width:100%;height:100%}
  .brand{position:absolute;left:250px;top:140px;display:flex;align-items:center;gap:18px}
  .brand__dot{width:100px;height:100px;border-radius:50%;background:var(--blue-navy)}
  .brand__name{font-size:32px;font-weight:500;color:var(--ink);letter-spacing:1px}
  .person{position:absolute;right:90px;top:90px;text-align:right}
  .person__name{font-size:28px;font-weight:600;letter-spacing:2px;text-transform:uppercase;color:var(--ink)}
  .person__role{font-size:16px;font-weight:500;letter-spacing:2px;text-transform:uppercase;color:var(--ink-soft);margin-top:4px}
  .contacts{position:absolute;left:60px;top:296px;list-style:none}
  .contacts__item{display:flex;align-items:center;gap:12px;font-size:18px;line-height:32px;color:var(--ink)}
  .contacts__icon{width:20px;height:20px;flex:none}
</style>
</head>
<body>
  <section class="card" aria-label="Tall Brook business card">
    <svg class="card__swoosh" viewBox="0 0 900 514" aria-hidden="true">
      <defs>
        <linearGradient id="bandBlue" x1="0" y1="1" x2="1" y2="0">
          <stop offset="0" stop-color="#22407f"/>
          <stop offset=".55" stop-color="#3176b5"/>
          <stop offset="1" stop-color="#22407f"/>
        </linearGradient>
      </defs>
      <path d="M440,484 Q600,440 720,350" fill="none" stroke="var(--steel-light)" stroke-width="2"/>
      <path d="M300,512 Q640,470 900,352" fill="none" stroke="var(--steel)" stroke-width="8"/>
      <path d="M360,514 Q660,480 900,378 L900,440 Q700,500 470,514 Z" fill="url(#bandBlue)"/>
      <path d="M560,514 Q760,488 900,458" fill="none" stroke="var(--steel)" stroke-width="3"/>
    </svg>

    <div class="brand">
      <span class="brand__dot"></span>
      <span class="brand__name">Tall Brook</span>
    </div>

    <div class="person">
      <p class="person__name">Marjorie Hadley</p>
      <p class="person__role">Security Installation</p>
    </div>

    <ul class="contacts">
      <li class="contacts__item">
        <svg class="contacts__icon" viewBox="0 0 20 20"><circle cx="10" cy="10" r="10" fill="var(--ink)"/><path d="M7 5.5l2 2-1 1.2a6 6 0 0 0 3.3 3.3l1.2-1 2 2-1.3 1.5C9.5 14 6 10.5 5.5 6.8z" fill="#fff"/></svg>
        012 555 0147
      </li>
      <li class="contacts__item">
        <svg class="contacts__icon" viewBox="0 0 20 20"><circle cx="10" cy="10" r="10" fill="var(--ink)"/><rect x="7" y="4.5" width="6" height="11" rx="1.2" fill="#fff"/><rect x="8" y="6" width="4" height="7" fill="var(--ink)"/></svg>
        012 555 0147
      </li>
      <li class="contacts__item">
        <svg class="contacts__icon" viewBox="0 0 20 20"><circle cx="10" cy="10" r="10" fill="var(--ink)"/><rect x="5" y="6.5" width="10" height="7" fill="#fff"/><path d="M5 6.5l5 4 5-4" fill="none" stroke="var(--ink)" stroke-width="1"/></svg>
        hello@tallbrookllc.com
      </li>
      <li class="contacts__item">
        <svg class="contacts__icon" viewBox="0 0 20 20"><circle cx="10" cy="10" r="10" fill="var(--ink)"/><circle cx="10" cy="10" r="5" fill="none" stroke="#fff" stroke-width="1.2"/><path d="M5 10h10M10 5v10" stroke="#fff" stroke-width="1"/></svg>
        www.tallbrookllc.com
      </li>
      <li class="contacts__item">
        <svg class="contacts__icon" viewBox="0 0 20 20"><circle cx="10" cy="10" r="10" fill="var(--ink)"/><path d="M10 4.5a3.5 3.5 0 0 1 3.5 3.5c0 2.5-3.5 7-3.5 7s-3.5-4.5-3.5-7A3.5 3.5 0 0 1 10 4.5z" fill="#fff"/><circle cx="10" cy="8" r="1.3" fill="var(--ink)"/></svg>
        281 Orchard Rise, Mapleton, WV 25871
      </li>
    </ul>
  </section>
</body>
</html>
```